Belmont Ridge Business Card Design Project

We have recently rebranded and would like to design new business cards that incorporate the corporate logo - double sided cards with corporate logo on one side and contact details on the other

Target Market(s)

Sophisticated and high net worth investors and finance industry professionals

Industry/Entity Type

Funds Management

Contact Information for Business Card

The card should prominently feature the company name and logo. Other details will be standard contact details for each staff member - name, address, phone, email, website

Colors
0054AA
0677BA
7BADD7
CADEEF
E8F1F8

Requirements
Must have
• Double-sided design with one side prominently featuring the corporate logo and the other side with all standard contact details

```html
<!DOCTYPE html>
<html lang="en">
<head>
<meta charset="utf-8">
<title>Belmont Ridge Business Card</title>
<link href="https://fonts.googleapis.com/css2?family=Jost:wght@400;500&family=Open+Sans:wght@400;600&display=swap" rel="stylesheet">
<style>
  :root {
    --backdrop: #acacac;
    --navy: #1f4572;
    --paper: #ffffff;
    --ink-grey: #707070;
    --title-grey: #6a6a6a;
  }
  * { box-sizing: border-box; margin: 0; padding: 0; }
  html, body { width: 1200px; height: 1000px; overflow: hidden; }
  body { background: var(--backdrop); position: relative; font-family: "Open Sans", Arial, sans-serif; }

  .card { position: absolute; width: 514px; height: 297px; }
  .card--front { left: 57px; top: 339px; background: var(--navy); display: flex; align-items: center; justify-content: center; }
  .card--back { left: 614px; top: 338px; background: var(--paper); }

  .wordmark { font-family: "Jost", Arial, sans-serif; font-weight: 500; text-transform: uppercase; letter-spacing: 0.08em; white-space: nowrap; }
  .wordmark--front { color: var(--paper); font-size: 28px; margin-top: 22px; }
  .wordmark--back { position: absolute; right: 40px; top: 246px; color: var(--navy); font-size: 17px; }

  .person { position: absolute; left: 44px; top: 68px; }
  .person__name { font-family: "Jost", Arial, sans-serif; font-weight: 400; font-size: 19px; letter-spacing: 0.09em; color: var(--navy); line-height: 1; text-transform: uppercase; }
  .person__role { font-family: "Jost", Arial, sans-serif; font-size: 9.5px; letter-spacing: 0.12em; color: var(--title-grey); text-transform: uppercase; margin-top: 5px; }
  .person__rule { width: 24px; height: 2px; background: var(--navy); margin-top: 5px; }

  .contact { position: absolute; left: 44px; color: var(--ink-grey); font-size: 14px; line-height: 17px; }
  .contact--direct { top: 130px; }
  .contact--address { top: 181px; }
  .contact--web { top: 248px; }
  .contact strong { font-weight: 600; }
</style>
</head>
<body>
  <section class="card card--front" aria-label="Card front">
    <div class="wordmark wordmark--front">Belmont Ridge</div>
  </section>

  <section class="card card--back" aria-label="Card back">
    <div class="person">
      <div class="person__name">Daniel Hartley</div>
      <div class="person__role">Portfolio Manager</div>
      <div class="person__rule"></div>
    </div>
    <div class="contact contact--direct">
      <strong>+02 9000 4417</strong><br>
      enquiries@belmont-ridge.com
    </div>
    <div class="contact contact--address">
      Level 14 Harbour House,<br>
      52 Kent Lane,<br>
      Sydney NSW 2000
    </div>
    <div class="contact contact--web"><strong>www.belmont-ridge.com</strong></div>
    <div class="wordmark wordmark--back">Belmont Ridge</div>
  </section>
</body>
</html>
```